Stationery Design Project

I need a stationary design for our company. we are based in Houston, TX and we are called Mira Vell Lending. And we are wanting to brand our MoneyMendPlus program, which includes our tax preparation and restoration, credit repair service. Although our business offers other programs, we are interested in mainly focusing on The MoneyMendPlus program. We are looking for way to brand our ourselves and I believe that a great stationery design will help in achieving this goal. Our logo design is blue and light blue. the slogan is orange.

Industry/Entity Type

Business

Requirements
Must have
• Address: 30871 Calloway Ln. B-22
Houston, TX 75419
Tel. 555-318-6207
Fax 555-294-7153
www.miravelllending.example
info@miravelllending.example
Our Slogan: Confidence, Renewed!

```html
<!DOCTYPE html>
<html lang="en">
<head>
<meta charset="utf-8">
<title>MoneyMendPlus Business Card</title>
<link rel="stylesheet" href="https://fonts.googleapis.com/css2?family=Tinos:wght@400;700&display=swap">
<style>
  :root {
    --backdrop: #e9e6e1;
    --card: #ffffff;
    --card-edge: #d2cdc6;
    --brand-blue: #1c5f9e;
    --band-light: #1a8fd0;
    --band-dark: #0d3a6b;
    --slogan-orange: #f39a2a;
    --navy: #163f66;
    --ink: #333a42;
    --rule: #c9ccd0;
    --frame-light: #c4d6ea;
  }
  * { box-sizing: border-box; margin: 0; padding: 0; }
  html, body {
    width: 1200px; height: 375px; overflow: hidden;
    background: var(--backdrop);
    font-family: "Tinos", "Times New Roman", serif;
    color: var(--ink);
  }
  .card {
    position: absolute; top: 30px;
    width: 555px; height: 315px;
    background: var(--card);
    border: 1px solid var(--card-edge);
  }
  .card--front { left: 32px; }
  .card--back { left: 612px; }

  /* Front */
  .brand-name {
    position: absolute; left: 0; right: 0; top: 92px;
    text-align: center;
    font-size: 46px; font-weight: 400; line-height: 56px;
    color: var(--brand-blue);
    letter-spacing: -0.5px;
  }
  .slogan-band {
    position: absolute; left: 0; right: 0; top: 161px; height: 42px;
    border-top: 2px solid var(--slogan-orange);
    border-bottom: 2px solid var(--slogan-orange);
    padding: 4px 0;
  }
  .slogan-band__bar {
    height: 100%;
    background: linear-gradient(90deg, var(--band-light), var(--band-dark));
    color: #fff;
    font-weight: 700; font-size: 18px; letter-spacing: 1.6px;
    display: flex; align-items: center; justify-content: center;
    padding-right: 10px;
  }
  .address {
    position: absolute; right: 323px; top: 242px;
    text-align: right; font-size: 14.5px; line-height: 19px;
    font-style: normal;
  }
  .contact-divider {
    position: absolute; left: 254px; top: 217px;
    width: 1px; height: 90px; background: var(--rule);
  }
  .contact-list {
    position: absolute; left: 274px; top: 220px;
    list-style: none; font-size: 14.5px;
  }
  .contact-list li {
    display: flex; align-items: center; gap: 7px;
    height: 22px;
  }
  .contact-list svg { width: 12px; height: 12px; fill: var(--navy); flex: none; }

  /* Back */
  .mark-block {
    position: absolute; left: 168px; top: 34px;
    width: 218px; height: 218px;
    background: var(--frame-light);
    padding: 7px;
  }
  .mark-block__square {
    width: 100%; height: 100%;
    background: var(--navy);
    position: relative;
  }
  .mark-block__name {
    position: absolute; left: 0; right: 0; bottom: 30px;
    text-align: center;
    font-size: 17px; color: #fff; font-weight: 400;
  }
  .back-web {
    position: absolute; left: 0; right: 0; top: 279px;
    text-align: center; font-size: 14.5px; letter-spacing: 2.6px;
    color: var(--navy);
  }
  .back-web strong { font-weight: 700; }
</style>
</head>
<body>
  <section class="card card--front" aria-label="Front of business card">
    <div class="brand-name">MoneyMendPlus</div>

    <div class="slogan-band">
      <div class="slogan-band__bar">Confidence, Renewed!</div>
    </div>

    <address class="address">
      30871 Calloway Ln. B-22<br>
      Houston, TX 75419
    </address>

    <div class="contact-divider"></div>

    <ul class="contact-list">
      <li>
        <svg viewBox="0 0 24 24" aria-label="Phone"><path d="M6.6 10.8a15 15 0 0 0 6.6 6.6l2.2-2.2a1 1 0 0 1 1-.25 11.4 11.4 0 0 0 3.6.57 1 1 0 0 1 1 1V20a1 1 0 0 1-1 1A17 17 0 0 1 3 4a1 1 0 0 1 1-1h3.5a1 1 0 0 1 1 1c0 1.25.2 2.45.57 3.57a1 1 0 0 1-.25 1z"/></svg>
        555-318-6207
      </li>
      <li>
        <svg viewBox="0 0 24 24" aria-label="Fax"><path d="M6 2h10l2 2v5H6zM3 10h18a1 1 0 0 1 1 1v7h-4v4H6v-4H2v-7a1 1 0 0 1 1-1zm5 7v3h8v-3z"/></svg>
        555-294-7153
      </li>
      <li>
        <svg viewBox="0 0 24 24" aria-label="Email"><path d="M2 5h20v14H2zm2 2v.4l8 5.2 8-5.2V7zm0 2.8V17h16V9.8l-8 5.2z"/></svg>
        info@miravelllending.example
      </li>
      <li>
        <svg viewBox="0 0 24 24" aria-label="Website"><path d="M12 2a10 10 0 1 0 0 20 10 10 0 0 0 0-20zm6.9 6h-3a15 15 0 0 0-1.3-3.9A8 8 0 0 1 18.9 8zM12 4c.8 1.1 1.5 2.5 1.9 4h-3.8c.4-1.5 1.1-2.9 1.9-4zM4.3 14a8 8 0 0 1 0-4h3.4a16 16 0 0 0 0 4zm.8 2h3a15 15 0 0 0 1.3 3.9A8 8 0 0 1 5.1 16zm3-8h-3a8 8 0 0 1 4.3-3.9A15 15 0 0 0 8.1 8zM12 20c-.8-1.1-1.5-2.5-1.9-4h3.8c-.4 1.5-1.1 2.9-1.9 4zm2.3-6H9.7a14 14 0 0 1 0-4h4.6a14 14 0 0 1 0 4zm.3 5.9a15 15 0 0 0 1.3-3.9h3a8 8 0 0 1-4.3 3.9zm1.7-5.9a16 16 0 0 0 0-4h3.4a8 8 0 0 1 0 4z"/></svg>
        www.miravelllending.example
      </li>
    </ul>
  </section>

  <section class="card card--back" aria-label="Back of business card">
    <div class="mark-block">
      <div class="mark-block__square">
        <div class="mark-block__name">Mira Vell Lending</div>
      </div>
    </div>
    <div class="back-web">www.<strong>miravelllending</strong>.example</div>
  </section>
</body>
</html>
```